Branding Assistance needed for Business Consultantcy expansion

Looking for some key branding components to assist with the expansion of our company into business consultancy work.
Existing company is an Accountancy firm (Marrowfield Accountants) and we have set up a new Company (TrellVane) which is the Business Consultancy arm.
We offer an Accountancy & Business Consultancy service and believe strongly in helping people achieve their dreams through business success.

Marrowfield focusses on Taxation, Compliance & Restructure work.
TrellVane will focus on Business Development and Enhancement (Sales, Marketing, Systems & Planning)

I need to develop some General branding Tools across the 2 x arms.
We are all about fixing Business Problems.

Specifically I need:
1 x New Logo Design (For TrellVane)
4 x Product/Feature Icon Designs
1 x Pull Up Banner Design

Logo Design
This is purely a new Logo for Trellvane.

4 x Icon Designs..
...that I can use on business cards, posters signs etc.
The aim of the Icons is to have a consistent look and feel around our messaging.
If it helps, the basic messaging we are trying to get across is:
We help your business Perform
So you can create Wealth and stability
So to impact your Lifestyle
And enable you to reach your Goals & Dreams
The words to go with each Icon are (in brackets I have put my iinitial ideas of what the icon might represent):
Performance (Graph/Chart on the increase?)
Wealth (Dollar sign?)
Lifestyle (Family time?)
Dreams (future/sunset?)
(I have attached some images that may help with the concept but feel free to go left field)

Pull Up Banner Design
Looking for a great design for a Pull up Banner measuring 850mm wide and 2000mm high.

The current text we have in mind is... (But will probably change)

“Less time working…more time living.”

“What would you rather be doing?” (MAIN MESSAGE)
4 Icons
“Let us take you there”

Then include some imagery for Success, Performance, Family, Goals/Dreams, Holidays??

Our Logo for the Accountancy side of the business (Marrowfield Accountants) is traditionally Blue with complementing colours usually being Gold and lighter browns.
On the business consultancy (TrellVane) side of things we will probably lend itself to greens and browns. (See sample Logo)
But happy to consider new pallets.

I have increased the budget for 1st prize to $300

I am extending deadline until tommorrow to give everyone a chance to finish off their works.
Hope this helps.

Target Market(s)

Small to Medium Business Owners (usually Family owned businesses)

Industry/Entity Type

Business

Requirements
Must have
• TrellVane Logo
Must capture the essence of the name and what we do. TrellVane (as in Landscaping your business) Tag line would be "Revive, Redesign, Revitalize your Business"

Icons
Consistency across the 4 icons, so if a caricature icon of a dollar sign is used with a Bold Border, then same concept carried through on other Icons.

Pull Up Banner
To fit dimensions 850mm by 2000mm
Note: please allow for 30mm bleed at Top and 150mm bleed at bottom.
Should not have
• Should not be just another "corporate" look and feel.
Needs to be vibrant and stand out.

```html
<!DOCTYPE html>
<html lang="en">
<head>
<meta charset="utf-8">
<title>TrellVane Pull Up Banner</title>
<link rel="stylesheet" href="https://fonts.googleapis.com/css2?family=Anton&family=Archivo+Black&family=Arimo:wght@400;700&family=Marcellus&display=swap">
<style>
  :root {
    --teal: #1c6584;
    --teal-dark: #155571;
    --green: #4cbf14;
    --white: #ffffff;
    --ink: #111111;
    --sky-top: #c9dde8;
    --sky-mid: #6fa3c6;
    --sky-low: #b9d3e3;
    --grass: #5fa92a;
    --grass-dark: #3f7d1a;
  }
  html, body {
    margin: 0;
    padding: 0;
    width: 1200px;
    height: 2824px;
    overflow: hidden;
    background: var(--white);
  }
  .banner {
    position: relative;
    width: 1200px;
    height: 2824px;
    overflow: hidden;
    background: var(--white);
    font-family: "Arimo", Arial, sans-serif;
  }
  .top-clouds {
    position: absolute;
    left: 0; top: 0;
    width: 1200px; height: 290px;
    background: linear-gradient(160deg, #b7d0de 0%, #e4eef4 35%, rgba(255,255,255,0) 70%);
  }
  .scene-photo {
    position: absolute;
    left: 0; top: 1260px;
    width: 1200px; height: 1564px;
    background: linear-gradient(180deg,
      rgba(255,255,255,1) 0%,
      var(--sky-top) 14%,
      var(--sky-mid) 34%,
      #8db8d4 55%,
      var(--sky-low) 76%,
      var(--grass) 78%,
      var(--grass-dark) 100%);
  }
  .brand {
    position: absolute;
    text-align: center;
  }
  .brand-name {
    font-family: "Archivo Black", Arial, sans-serif;
    letter-spacing: 2px;
    line-height: 1;
  }
  .brand--top { left: 470px; top: 132px; width: 620px; }
  .brand--top .brand-name { font-size: 104px; color: var(--teal); }
  .brand--top .brand-tagline {
    font-size: 27px; color: #333; margin-top: 6px;
  }
  .brand--bottom { left: 160px; top: 2548px; width: 880px; }
  .brand--bottom .brand-name { font-size: 112px; color: var(--white); }
  .brand--bottom .brand-tagline {
    font-family: "Anton", Impact, sans-serif;
    font-size: 44px; color: var(--ink); margin-top: 14px; letter-spacing: 1px;
  }
  .headline {
    position: absolute;
    margin: 0;
    line-height: 1;
    white-space: nowrap;
  }
  .headline .soft { font-family: "Marcellus", Georgia, serif; font-weight: 400; font-size: 110px; }
  .headline .strong { font-family: "Archivo Black", Arial, sans-serif; font-size: 112px; }
  .headline--work { left: 108px; top: 420px; color: var(--teal); }
  .headline--live { left: 234px; top: 586px; color: var(--green); }
  .question-band {
    position: absolute;
    left: 36px; top: 764px;
    width: 1156px; height: 176px;
  }
  .question {
    position: absolute;
    left: 0; top: 820px;
    width: 1240px;
    text-align: center;
    margin: 0;
    color: var(--white);
    font-size: 62px;
    letter-spacing: -1px;
  }
  .question .mark { font-family: "Archivo Black", Arial, sans-serif; }
  .value {
    position: absolute;
    text-align: center;
    color: var(--teal);
    font-size: 30px;
  }
  .value-icon {
    margin: 0 auto 10px;
    border-radius: 24px;
    background: linear-gradient(135deg, rgba(76,191,20,.28), rgba(28,101,132,.28));
  }
  .value--performance { left: 30px; top: 1200px; width: 220px; }
  .value--performance .value-icon { width: 200px; height: 120px; }
  .value--wealth { left: 384px; top: 1090px; width: 220px; }
  .value--wealth .value-icon { width: 200px; height: 176px; }
  .value--family { left: 664px; top: 1220px; width: 220px; }
  .value--family .value-icon { width: 166px; height: 150px; }
  .value--dreams { left: 904px; top: 1080px; width: 250px; }
  .value--dreams .value-icon { width: 250px; height: 120px; }
  .journey {
    position: absolute;
    left: 0; top: 1360px;
    width: 1200px; height: 1060px;
  }
</style>
</head>
<body>
<main class="banner">
  <div class="top-clouds" role="img" aria-label="Soft white clouds in a pale blue sky"></div>
  <div class="scene-photo" role="img" aria-label="Businessman seated in an office chair with arms outstretched in a green meadow under a blue sky with clouds"></div>

  <header class="brand brand--top">
    <div class="brand-name">TRELLVANE</div>
    <div class="brand-tagline">Revive, Redesign, Revitalize your Business.</div>
  </header>

  <h1 class="headline headline--work"><span class="soft">Less time </span><span class="strong">working...</span></h1>
  <h2 class="headline headline--live"><span class="soft">more time </span><span class="strong">living</span></h2>

  <svg class="question-band" viewBox="0 0 1156 176" aria-hidden="true">
    <path fill="var(--teal)" d="M20 40 L120 22 L300 30 L520 12 L760 26 L980 8 L1140 24 L1150 70 L1132 110 L1156 150 L980 164 L740 150 L520 172 L300 156 L110 170 L6 150 L22 110 L0 76 Z"/>
  </svg>
  <p class="question">What would you rather be doing<span class="mark">?</span></p>

  <div class="value value--performance">
    <div class="value-icon" role="img" aria-label="Green rising arrow chart icon"></div>Performance
  </div>
  <div class="value value--wealth">
    <div class="value-icon" role="img" aria-label="Green tree with dollar coins icon"></div>Wealth
  </div>
  <div class="value value--family">
    <div class="value-icon" role="img" aria-label="Family inside a heart icon"></div>Family
  </div>
  <div class="value value--dreams">
    <div class="value-icon" role="img" aria-label="Sun rising over hills icon"></div>Dreams
  </div>

  <svg class="journey" viewBox="0 0 1200 1060" aria-hidden="true">
    <polygon fill="var(--teal)" points="10,640 584,190 210,880"/>
    <polygon fill="var(--teal-dark)" points="150,1040 1110,14 300,880"/>
    <text x="0" y="0" transform="translate(214,900) rotate(-46.5)"
          font-family="Anton, Impact, sans-serif" font-size="112"
          textLength="1090" lengthAdjust="spacingAndGlyphs">
      <tspan fill="var(--white)">Let us take </tspan><tspan fill="var(--green)">you there</tspan>
    </text>
  </svg>

  <footer class="brand brand--bottom">
    <div class="brand-name">TRELLVANE</div>
    <div class="brand-tagline">Revive, Redesign, Revitalize your Business.</div>
  </footer>
</main>
</body>
</html>
```